Need Business Card for our Real Estate Business with Sales Executive's Picture

PANTONE 484 C ( RED)

PANTONE 2766 C ( BLUE

Industry/Entity Type

Real Estate

Contact Information for Business Card

Name, Mobile, email, & picture of Person
Agency Phone, address, Web address

Requirements
Must have
• Our Logo Colours, Agent Picture,

```html
<!DOCTYPE html>
<html lang="en">
<head>
<meta charset="utf-8">
<title>Meridian Real Estate – Business Card</title>
<link rel="stylesheet" href="https://fonts.googleapis.com/css2?family=Cinzel:wght@400&family=Open+Sans:wght@400;600&display=swap">
<style>
  :root {
    --navy: #101c4f;
    --navy-deep: #0c1642;
    --red: #8a1c2b;
    --white: #ffffff;
    --ink: #1a2250;
    --page: #e6e7ea;
    --photo-light: #f3f4f7;
    --photo-mid: #3c55a8;
  }
  * { box-sizing: border-box; margin: 0; padding: 0; }
  html, body { width: 1200px; height: 800px; overflow: hidden; }
  body {
    background: var(--page);
    display: flex;
    align-items: center;
    justify-content: center;
    gap: 34px;
    font-family: "Open Sans", sans-serif;
  }
  .card {
    position: relative;
    width: 560px;
    height: 320px;
    overflow: hidden;
    box-shadow: 0 10px 28px rgba(0,0,0,0.18);
  }

  /* Back side */
  .card-back {
    background: var(--navy-deep);
    color: var(--white);
    display: flex;
    flex-direction: column;
    align-items: center;
    justify-content: center;
  }
  .brand {
    display: flex;
    align-items: center;
    gap: 10px;
  }
  .brand-mark {
    width: 10px;
    height: 10px;
    background: var(--red);
  }
  .brand-name {
    font-family: "Cinzel", serif;
    font-weight: 400;
    letter-spacing: 4px;
    line-height: 1.05;
    text-align: center;
  }
  .card-back .brand-name { font-size: 44px; color: var(--white); }
  .card-back .brand-name small { display: block; font-size: 13px; letter-spacing: 5px; }
  .brand-rule {
    width: 300px;
    height: 1px;
    background: var(--white);
    margin: 14px 0 26px;
  }
  .back-web {
    font-size: 13px;
    letter-spacing: 3px;
  }

  /* Front side */
  .card-front { background: var(--white); }
  .agent-photo {
    position: absolute;
    left: 0; top: 0;
    width: 250px;
    height: 300px;
    background: linear-gradient(180deg, var(--photo-light) 0%, var(--photo-light) 35%, var(--photo-mid) 100%);
  }
  .front-content {
    position: absolute;
    left: 275px;
    top: 34px;
    width: 260px;
    color: var(--ink);
  }
  .card-front .brand-name {
    font-size: 38px;
    color: var(--ink);
    text-align: left;
  }
  .card-front .brand-name small { display: block; font-size: 11px; letter-spacing: 4px; text-align: right; }
  .front-rule {
    height: 1px;
    background: var(--ink);
    margin: 8px 0 20px;
  }
  .agent-name {
    font-size: 15px;
    font-weight: 600;
    letter-spacing: 0.5px;
    color: var(--ink);
  }
  .agent-role {
    font-size: 12px;
    color: var(--red);
    margin-bottom: 12px;
  }
  .address {
    font-size: 12px;
    line-height: 1.45;
    margin-bottom: 8px;
  }
  .contact-list { list-style: none; font-size: 12px; }
  .contact-list li {
    display: flex;
    align-items: center;
    gap: 8px;
    line-height: 1.6;
  }
  .contact-icon { width: 14px; height: 14px; flex: none; }
  .bottom-band {
    position: absolute;
    left: 0; bottom: 0;
    width: 100%;
    height: 20px;
    display: flex;
  }
  .band-navy { flex: 1; background: var(--navy); }
  .band-red { width: 110px; background: var(--red); }
</style>
</head>
<body>

  <section class="card card-back" aria-label="Card back">
    <div class="brand">
      <span class="brand-mark"></span>
      <div class="brand-name">MERIDIAN<small>REAL ESTATE</small></div>
    </div>
    <div class="brand-rule"></div>
    <p class="back-web">www.meridianhomes.com</p>
  </section>

  <section class="card card-front" aria-label="Card front">
    <div class="agent-photo" role="img" aria-label="Portrait photo of the agent in a blue suit"></div>

    <div class="front-content">
      <div class="brand-name">MERIDIAN<small>REAL ESTATE</small></div>
      <div class="front-rule"></div>

      <p class="agent-name">DANIEL HART</p>
      <p class="agent-role">Owner</p>

      <p class="address">PO BOX 456 Harbour Road<br>3rd street Geelong</p>

      <ul class="contact-list">
        <li>
          <svg class="contact-icon" viewBox="0 0 14 14" aria-hidden="true">
            <circle cx="7" cy="7" r="6.5" fill="var(--red)"/>
            <rect x="4.8" y="3" width="4.4" height="8" rx="0.8" fill="none" stroke="#fff" stroke-width="1"/>
          </svg>
          (123) 555-0147
        </li>
        <li>
          <svg class="contact-icon" viewBox="0 0 14 14" aria-hidden="true">
            <circle cx="7" cy="7" r="6.5" fill="var(--red)"/>
            <rect x="3.5" y="4.5" width="7" height="5" fill="none" stroke="#fff" stroke-width="1"/>
            <path d="M3.5 4.5 L7 7.5 L10.5 4.5" fill="none" stroke="#fff" stroke-width="1"/>
          </svg>
          info@meridianhomes.com
        </li>
        <li>
          <svg class="contact-icon" viewBox="0 0 14 14" aria-hidden="true">
            <circle cx="7" cy="7" r="6.5" fill="var(--red)"/>
            <circle cx="7" cy="7" r="3.6" fill="none" stroke="#fff" stroke-width="0.9"/>
            <path d="M3.4 7 H10.6 M7 3.4 C5.4 5.4 5.4 8.6 7 10.6 M7 3.4 C8.6 5.4 8.6 8.6 7 10.6" fill="none" stroke="#fff" stroke-width="0.8"/>
          </svg>
          www.meridianhomes.com
        </li>
      </ul>
    </div>

    <div class="bottom-band">
      <span class="band-navy"></span>
      <span class="band-red"></span>
    </div>
  </section>

</body>
</html>
```